Marava Cove Lodge Christmas wishes 2013

We require postcards designed to mail our to our clients for Christmas. We are a SURF travel company, with a high end market and like to mail our Christmas postcards to all our guests that have stayed with us through the year. Front cover will have images and text (ie Seasons Greeting) and our logo. The back will have space for TO: name & address and postage stamp. Will also have some basic text (ie The Management & Staff at Marava Cove Lodge wish you and your family all the best for the Festive Season and New Year. We look forward to seeing you back at Marava Cove Lodge again soon etc etc). Here is link to main image https://www.filecrate-example.com/sh/qwmxrtz481plo/Vb7kRtPwqN

Target Market(s)

Our clients are mostly mature men (40-70) surfers who purchase luxury surf trips

Industry/Entity Type

Travel

Requirements
Must have
• Ocean Image (front)
Logo x 2 in same colour - Orindel & Marava Cove Lodge (front)
Text (front)
Back to be white
Space for name & address (back)
Space for postage stamp (back)
Message (back)
Website www.orindellodges-example.com (back)

```html
<!DOCTYPE html>
<html lang="en">
<head>
<meta charset="utf-8">
<title>Marava Cove Lodge – Season's Greetings Postcard</title>
<link href="https://fonts.googleapis.com/css2?family=Arimo:wght@700&family=Montserrat:wght@400&family=Poiret+One&display=swap" rel="stylesheet">
<style>
  :root {
    --backdrop: #ececec;
    --card-white: #ffffff;
    --ocean-deep: #0b2f6e;
    --ocean-teal: #1f8f8a;
    --ocean-green: #2fb59a;
    --sky-blue: #1c5fd0;
    --foam: #d8eef2;
    --mark-white: #ffffff;
    --ink-grey: #8a8a8a;
    --rule-grey: #c4c4c4;
  }
  * { margin: 0; padding: 0; box-sizing: border-box; }
  html, body { width: 1200px; height: 1000px; overflow: hidden; }
  body { background: var(--backdrop); position: relative; }

  .postcard { position: absolute; width: 563px; height: 375px; overflow: hidden; }

  /* Front */
  .postcard--front { left: 324px; top: 58px; }
  .front-photo {
    position: absolute; inset: 0;
    background:
      radial-gradient(ellipse 45% 60% at 62% 30%, var(--foam) 0%, rgba(216,238,242,0) 60%),
      linear-gradient(180deg, rgba(28,95,208,0) 55%, var(--ocean-deep) 100%),
      linear-gradient(100deg, var(--ocean-teal) 0%, var(--ocean-green) 40%, var(--sky-blue) 75%, var(--ocean-deep) 100%);
  }
  .front-greeting {
    position: absolute; left: 56px; top: 44px;
    font-family: "Arimo", Arial, sans-serif; font-weight: 700;
    font-size: 22px; color: var(--mark-white); letter-spacing: -0.3px;
  }
  .lodge-mark {
    position: absolute; left: 118px; top: 314px; width: 100px;
    text-align: center; color: var(--mark-white);
    font-family: "Montserrat", Arial, sans-serif; font-weight: 400;
  }
  .lodge-mark__row { display: flex; align-items: center; justify-content: center; gap: 5px; }
  .lodge-mark__dot { width: 14px; height: 14px; border: 1.5px solid var(--mark-white); border-radius: 50%; }
  .lodge-mark__name { font-size: 10px; white-space: nowrap; }
  .lodge-mark__url { font-size: 7.5px; margin-top: 3px; white-space: nowrap; }
  .lodge-mark__region { font-size: 7px; letter-spacing: 1.5px; margin-top: 2px; }
  .brand-mark {
    position: absolute; left: 288px; top: 328px;
    font-family: "Montserrat", Arial, sans-serif; font-weight: 400;
    font-size: 10.5px; letter-spacing: 1.6px; color: var(--mark-white);
    display: flex; align-items: center; gap: 8px;
  }
  .brand-mark__dot { width: 12px; height: 12px; background: var(--mark-white); border-radius: 50%; }

  /* Back */
  .postcard--back { left: 325px; top: 509px; background: var(--card-white); }
  .back-message {
    position: absolute; left: 30px; top: 45px; width: 229px;
    font-family: "Poiret One", cursive; font-size: 11.2px; line-height: 16.5px;
    color: var(--ink-grey); text-align: justify;
  }
  .back-message p + p { margin-top: 17px; }
  .back-website {
    position: absolute; left: 30px; top: 329px; width: 229px; text-align: center;
    font-family: "Poiret One", cursive; font-size: 14px; color: var(--ink-grey);
  }
  .back-divider { position: absolute; left: 283px; top: 22px; width: 1px; height: 332px; background: var(--rule-grey); }
  .stamp-box {
    position: absolute; left: 489px; top: 20px; width: 45px; height: 71px;
    border: 1px dotted var(--ink-grey); padding: 3px;
  }
  .stamp-box__inner { width: 100%; height: 100%; border: 1px solid var(--rule-grey); }
  .address-line { position: absolute; left: 315px; width: 210px; height: 1px; background: var(--rule-grey); }
</style>
</head>
<body>
  <section class="postcard postcard--front">
    <div class="front-photo" role="img" aria-label="Photograph of a surfer riding inside a curling turquoise wave under a clear blue sky, with mountains on the horizon"></div>
    <h1 class="front-greeting">Seasons Greetings!</h1>
    <div class="lodge-mark">
      <div class="lodge-mark__row"><span class="lodge-mark__dot"></span><span class="lodge-mark__name">Marava Cove Lodge</span></div>
      <div class="lodge-mark__url">maravacovelodge-example.com</div>
      <div class="lodge-mark__region">indonesia</div>
    </div>
    <div class="brand-mark"><span class="brand-mark__dot"></span><span>ORINDEL LODGES &amp; RESORTS</span></div>
  </section>

  <section class="postcard postcard--back">
    <div class="back-message">
      <p>The Management &amp; Staff at Marava Cove Lodge wish you and your family all the best for the Festive Season and New Year.</p>
      <p>We look forward to seeing you back at Marava Cove Lodge again soon!</p>
    </div>
    <div class="back-website">www.orindellodges-example.com</div>
    <div class="back-divider"></div>
    <div class="stamp-box"><div class="stamp-box__inner"></div></div>
    <div class="address-line" style="top:188px"></div>
    <div class="address-line" style="top:218px"></div>
    <div class="address-line" style="top:248px"></div>
    <div class="address-line" style="top:278px"></div>
  </section>
</body>
</html>
```